Corvane Freight Company Business Card Design

We are a company that delivers natural saltwater (from the ocean) to aquarium companies, restaurants and home marine tanks. I would like a new business card to suit.

Must include Name, company name, abn, contact number and website as well as logo (see attached).

Looking for a design that stands out, has a clean but unique appearance.

Double and single sided entries welcome

Business

• Logo

```html
<!DOCTYPE html>
<html lang="en">
<head>
<meta charset="utf-8">
<title>Corvane Freight Company Business Card</title>
<link rel="stylesheet" href="https://fonts.googleapis.com/css2?family=Open+Sans:wght@400;600;700&display=swap">
<style>
  :root {
    --page-top: #b9b9b9;
    --page-bottom: #ececec;
    --card-blue: #3052a1;
    --wave-blue: #4fc8f2;
    --wave-light: #9fe2f8;
    --white: #ffffff;
    --ink-soft: #e6ecf7;
  }
  * { margin: 0; padding: 0; box-sizing: border-box; }
  html, body { width: 1200px; height: 900px; overflow: hidden; }
  body {
    background: linear-gradient(180deg, var(--page-top), var(--page-bottom));
    font-family: "Open Sans", Arial, sans-serif;
    position: relative;
  }
  .card {
    position: absolute;
    top: 300px;
    width: 520px;
    height: 300px;
    background: var(--card-blue);
    color: var(--white);
    overflow: hidden;
    box-shadow: 0 10px 30px rgba(0,0,0,0.25);
  }
  .card--back { left: 60px; }
  .card--front { left: 620px; }

  .back-brand {
    position: absolute;
    top: 90px; left: 0; right: 0;
    text-align: center;
    font-size: 46px;
    font-weight: 700;
    color: var(--white);
    letter-spacing: -0.5px;
  }
  .back-url {
    position: absolute;
    top: 200px; left: 0; right: 0;
    text-align: center;
    font-size: 22px;
    font-weight: 700;
  }

  .front-top {
    position: absolute;
    top: 0; left: 0;
    width: 520px; height: 88px;
    display: block;
  }
  .holder {
    position: absolute;
    top: 94px; left: 30px;
  }
  .holder-name { font-size: 28px; font-weight: 600; line-height: 1.15; }
  .holder-role { font-size: 16px; font-weight: 600; line-height: 1.2; }

  .contacts {
    position: absolute;
    top: 164px; left: 30px;
    display: grid;
    grid-template-columns: 62px auto;
    font-size: 11.5px;
    line-height: 14px;
    color: var(--ink-soft);
  }
  .contacts dt { font-weight: 600; }
  .contacts .gap { margin-top: 7px; }

  .front-brand {
    position: absolute;
    top: 180px; right: 24px;
    font-size: 24px;
    font-weight: 700;
    color: var(--white);
    text-align: right;
    line-height: 1.1;
  }
</style>
</head>
<body>
  <section class="card card--back" aria-label="Card back">
    <div class="back-brand">Corvane Freight</div>
    <div class="back-url">www.corvanefreight.com</div>
  </section>

  <section class="card card--front" aria-label="Card front">
    <svg class="front-top" viewBox="0 0 520 88" preserveAspectRatio="none" role="img" aria-label="Light blue ocean wave illustration across the top of the card">
      <defs>
        <linearGradient id="waveTone" x1="0" y1="0" x2="0" y2="1">
          <stop offset="0" stop-color="#9fe2f8"/>
          <stop offset="1" stop-color="#4fc8f2"/>
        </linearGradient>
      </defs>
      <rect width="520" height="88" fill="#ffffff"/>
      <rect y="26" width="520" height="62" fill="url(#waveTone)"/>
    </svg>

    <div class="holder">
      <div class="holder-name">Name Surname</div>
      <div class="holder-role">Position</div>
    </div>

    <dl class="contacts">
      <dt>Address</dt><dd>#123 Lorem Street, Dolor sit City, PA 19017</dd>
      <dt>Office</dt><dd>098.765.4321</dd>
      <dt class="gap">Mobile</dt><dd class="gap">123.456.7890</dd>
      <dt>E-mail</dt><dd>name@corvanefreight.com</dd>
      <dt>Facebook</dt><dd>corvanefreight</dd>
      <dt>Twitter</dt><dd>corvanefreight</dd>
      <dt class="gap">Website</dt><dd class="gap">www.corvanefreight.com</dd>
    </dl>

    <div class="front-brand">Corvane<br>Freight</div>
  </section>
</body>
</html>
```